I would like a minimalist clean and uncluttered website design.
Initially, I would like to see a front page only and would then like to build on the project front there.
DVQ logo file with no background is attached, can be grey scale if the designer wishes.
I would like the front page to speak about the company's ethos and goals and I will need to put a great deal of thought into this to ensure it has the desired impact with the content on the subsequent pages.
The paragraph below gives a bit of an idea as to what this will include.
"DVQ is a technology company providing approachable IT products and services to business:
With the overwhelming advancements in technology, businesses often find it difficult to determine what is available and what best suits their businesses specific needs.
We can assist business with their IT infrustucture, devices, software in procurement, installation, training, cost control as well as ongoing administration and support. We also keep our Clients informed of new technology and products which can benefit them"
Target Market(s)
Business, Health, Education, Professional Practices. Target age would be around 30 plus either male or female. Office administration level through Managing Directors. English speaking.

```html
<!DOCTYPE html>
<html lang="en">
<head>
<meta charset="utf-8">
<title>DVQ — Approachable IT for business</title>
<link href="https://fonts.googleapis.com/css2?family=Questrial&family=Open+Sans:ital,wght@0,300;0,400;0,600;1,300&display=swap" rel="stylesheet">
<style>
  :root{
    --green:#8dba3f;
    --navy:#2e3f7f;
    --bar:#2f3237;
    --hero-dark:#2a2c2f;
    --grey-text:#9a9a9a;
    --line:#c9c9c9;
    --footer:#34498a;
    --footer-text:#c9d0e6;
    --footer-accent:#b9c45a;
    --white:#ffffff;
  }
  *{margin:0;padding:0;box-sizing:border-box}
  html,body{width:1200px;height:1162px;overflow:hidden;background:var(--white)}
  body{position:relative;font-family:"Open Sans",sans-serif}
  a{text-decoration:none;color:inherit}

  .site-header{position:absolute;left:0;top:0;width:1200px;height:69px;background:var(--bar);border-top:3px solid #3b4f91;border-bottom:1px solid #1f2124}
  .brand{position:absolute;left:205px;top:14px;display:flex;align-items:center;gap:8px}
  .brand-mark{width:26px;height:26px;background:var(--green)}
  .brand-name{font-family:"Questrial",sans-serif;font-size:26px;color:var(--white);letter-spacing:3px}
  .main-nav{position:absolute;left:450px;top:24px;display:flex;gap:0}
  .main-nav a{font-size:14.5px;color:#a9adb3;margin-right:26px}
  .main-nav a.active{color:var(--green)}
  .account{position:absolute;left:890px;top:25px;display:flex;align-items:center;gap:13px;font-size:12px;color:var(--white)}
  .account .login{background:var(--green);color:#2f3a1c;padding:1px 8px;border-radius:2px}

  .hero{position:absolute;left:0;top:69px;width:1200px;height:341px;background:radial-gradient(ellipse at 50% 40%,#55585c 0%,#3a3c3f 55%,var(--hero-dark) 100%)}
  .hero h1{position:absolute;left:199px;top:96px;font-family:"Questrial",sans-serif;font-weight:400;font-size:27px;color:var(--green)}
  .hero p{position:absolute;left:200px;top:134px;font-style:italic;font-weight:300;font-size:15px;line-height:21.5px;color:var(--white)}
  .hero .cta{position:absolute;left:206px;top:198px;width:108px;height:30px;border:2px solid var(--white);color:var(--white);font-size:11px;display:flex;align-items:center;justify-content:center}
  .hero-photo{position:absolute;left:604px;top:3px;width:396px;height:338px;border-radius:120px 120px 20px 20px;background:linear-gradient(180deg,#6b5444 0%,#a8c2de 45%,#c7d9ee 100%)}

  .services h2{position:absolute;left:0;width:1172px;top:436px;text-align:center;font-family:"Questrial",sans-serif;font-weight:400;font-size:42px;color:var(--green)}
  .service{position:absolute;width:230px}
  .service h3{display:flex;align-items:center;gap:7px;font-weight:400;font-size:16px;color:var(--navy);height:22px}
  .service h3 svg{width:24px;height:22px}
  .service p{margin-top:8px;font-size:10px;font-weight:300;line-height:13.6px;color:var(--grey-text)}

  .clients-title{position:absolute;left:200px;top:787px;font-family:"Questrial",sans-serif;font-size:14.5px;color:#555}
  .clients-rule{position:absolute;left:286px;top:797px;width:716px;height:1px;background:var(--line)}
  .client-row{position:absolute;left:200px;top:842px;width:802px;height:38px;display:flex;align-items:center;justify-content:space-between}
  .arrow{width:10px;height:16px}
  .client{display:flex;align-items:center;gap:6px;font-family:"Open Sans",sans-serif;font-size:20px;font-weight:400;color:#7b7b7b}
  .client i{width:20px;height:20px;border-radius:50%;border:2px solid #9a9a9a;display:block}

  .site-footer{position:absolute;left:0;top:948px;width:1200px;height:214px;background:var(--footer);border-top:4px solid var(--green)}
  .footer-col{position:absolute;top:46px}
  .footer-col h4{font-family:"Questrial",sans-serif;font-weight:400;font-size:15.5px;color:#dfe4f2;margin-bottom:10px}
  .about p{width:250px;font-size:10px;line-height:13.6px;color:var(--footer-accent)}
  .quick ul{list-style:none;padding-left:4px}
  .quick li{font-size:10px;line-height:16.8px;color:var(--footer-text)}
  .quick li.active{color:var(--green)}
  .contact dl{font-size:10px;color:#e3e7f3;line-height:14px}
  .contact .row{display:flex;gap:40px;margin-top:4px}
  .contact .row div{width:79px}
  .contact .row div+div{width:auto}
  .footer-base{position:absolute;left:0;top:168px;width:1200px;border-top:1px solid #2c3f7b;height:42px}
  .footer-base small{position:absolute;left:201px;top:12px;font-size:10px;color:#c9d0e6}
  .social{position:absolute;left:830px;top:14px;display:flex;gap:14px}
  .social span{width:12px;height:12px;border-radius:50%;background:#aab3cf;display:block}
  .social svg{width:12px;height:12px}
</style>
</head>
<body>

<header class="site-header">
  <a class="brand" href="#"><span class="brand-mark"></span><span class="brand-name">DVQ</span></a>
  <nav class="main-nav">
    <a class="active" href="#">Home</a><a href="#">Services</a><a href="#">Project</a><a href="#">Articles</a><a href="#">Contact</a>
  </nav>
  <div class="account"><a class="login" href="#">Log in</a><a href="#">sign up</a></div>
</header>

<section class="hero">
  <h1>Welcome to Devqora</h1>
  <p>DVQ is a technology company providing<br>approachable IT products and services to business.</p>
  <a class="cta" href="#">LEARN MORE</a>
  <div class="hero-photo" role="img" aria-label="Smiling man in a light blue shirt giving two thumbs up"></div>
</section>

<section class="services">
  <h2>Our Services</h2>

  <article class="service" style="left:200px;top:531px">
    <h3><svg viewBox="0 0 24 22"><rect x="1" y="3" width="6" height="16" fill="none" stroke="#333" stroke-width="1.5"/><rect x="9" y="3" width="14" height="10" fill="none" stroke="#333" stroke-width="1.5"/><rect x="9" y="15" width="14" height="4" fill="#333"/></svg>IT infrustucture</h3>
    <p>Lorem Ipsum is simply dummy text of the printing and typesetting industry. Lorem Ipsum has been the industry's standard dummy text ever since the 1500s...</p>
  </article>
  <article class="service" style="left:489px;top:531px">
    <h3><svg viewBox="0 0 24 22"><rect x="7" y="2" width="10" height="19" rx="1.5" fill="none" stroke="#333" stroke-width="1.6"/><rect x="9" y="5" width="6" height="6" fill="#333"/></svg>Devices</h3>
    <p>Lorem Ipsum is simply dummy text of the printing and typesetting industry. Lorem Ipsum has been the industry's standard dummy text ever since the 1500s...</p>
  </article>
  <article class="service" style="left:782px;top:531px">
    <h3><svg viewBox="0 0 24 22"><rect x="2" y="1" width="20" height="20" rx="3" fill="none" stroke="#222" stroke-width="2"/><circle cx="12" cy="11" r="5" fill="none" stroke="#222" stroke-width="2.5" stroke-dasharray="3 1.5"/><circle cx="12" cy="11" r="2" fill="#222"/></svg>software</h3>
    <p>Lorem Ipsum is simply dummy text of the printing and typesetting industry. Lorem Ipsum has been the industry's standard dummy text ever since the 1500s...</p>
  </article>
  <article class="service" style="left:200px;top:651px">
    <h3><svg viewBox="0 0 24 22"><path d="M2 20 L20 4 L23 7 L6 21 Z" fill="none" stroke="#333" stroke-width="1.5"/><path d="M1 21 H22" stroke="#333" stroke-width="1.2"/></svg>Installation</h3>
    <p>Lorem Ipsum is simply dummy text of the printing and typesetting industry. Lorem Ipsum has been the industry's standard dummy text ever since the 1500s...</p>
  </article>
  <article class="service" style="left:489px;top:651px">
    <h3><svg viewBox="0 0 24 22"><circle cx="8" cy="3" r="2.5" fill="#222"/><circle cx="16" cy="3" r="2.5" fill="#222"/><path d="M5 7h6v7H9.5v8h-3v-8H5z M13 7h6v7h-1.5v8h-3v-8H13z" fill="#222"/></svg>Training</h3>
    <p>Lorem Ipsum is simply dummy text of the printing and typesetting industry. Lorem Ipsum has been the industry's standard dummy text ever since the 1500s...</p>
  </article>
  <article class="service" style="left:782px;top:651px">
    <h3><svg viewBox="0 0 24 22"><circle cx="12" cy="11" r="9" fill="none" stroke="#333" stroke-width="1.6"/><path d="M15 7.5c-1-1-5-1.5-5 1s5 1.5 5 4-4 2.5-6 1M12 5v12" fill="none" stroke="#333" stroke-width="1.6"/></svg>Cost cantrol</h3>
    <p>Lorem Ipsum is simply dummy text of the printing and typesetting industry. Lorem Ipsum has been the industry's standard dummy text ever since the 1500s...</p>
  </article>
</section>

<section class="clients">
  <h3 class="clients-title">Our Clients</h3>
  <div class="clients-rule"></div>
  <div class="client-row">
    <svg class="arrow" viewBox="0 0 10 16"><path d="M8 2 2 8l6 6" fill="none" stroke="#aaa" stroke-width="1.5"/></svg>
    <span class="client"><i></i>Brightnode</span>
    <span class="client">Larkhill</span>
    <span class="client">Infora</span>
    <span class="client">Brewline</span>
    <span class="client">Ovaline</span>
    <svg class="arrow" viewBox="0 0 10 16"><path d="M2 2l6 6-6 6" fill="none" stroke="#aaa" stroke-width="1.5"/></svg>
  </div>
</section>

<footer class="site-footer">
  <div class="footer-col about" style="left:201px">
    <h4>About us</h4>
    <p>Lorem ipsum dolor sit amet, consectetur adipisicing elit, sed do eiusmod tempor incididunt ut labore et dolore magna aliqua. Ut enim ad minim veniam, quis nostrud exercitation ullamco laboris nisi ut aliquip ex ea commodo consequat. Duis aute irure dolor.</p>
  </div>
  <div class="footer-col quick" style="left:525px">
    <h4>Quick likes</h4>
    <ul><li class="active">Home</li><li>Services</li><li>Project</li><li>Articles</li><li>Contact</li></ul>
  </div>
  <div class="footer-col contact" style="left:697px">
    <h4>Contact</h4>
    <dl>
      <dt>Address:</dt>
      <dd style="margin-top:4px">48 Harbour Lane, Kestrel Bay 3100 Australia</dd>
      <div class="row"><div>Phone:</div><div>Email:</div></div>
      <div class="row" style="margin-top:6px;line-height:10px"><div>+61 3 5550 0142<br>+61 3 5550 0187</div><div>info@devqora.com<br>support@devqora.com</div></div>
    </dl>
  </div>
  <div class="footer-base">
    <small>Copyright © 2013 Devqora.</small>
    <div class="social">
      <svg viewBox="0 0 12 12"><rect x="0.5" y="2" width="11" height="8" fill="#aab3cf"/><path d="M0.5 2 6 7l5.5-5" fill="none" stroke="#34498a"/></svg>
      <span></span><span></span><span></span><span></span><span></span><span></span>
    </div>
  </div>
</footer>

</body>
</html>
```